Varelko App for Smart Devices IoT WiFi Electronic

Varelko is a siren manufacturer. This application is used for the company's products that have a Wi-Fi connection and an internet connection, which can be configured and activated remotely through this application. In addition, this application is used to activate the siren at specific times for the start and end of shifts in companies and schools. Users will be siren installers and IT or HR managers.
In addition to activating motorized sirens timers, some siren models have speakers and allow you to play TTS (text to speech) audio, audio recorded by the user on the phone and upload audio (mp3) with playlist programming with start and end times.
Application screens: home with dashboard (one dashboard for each category). Device categories: timers, speakers, motorized siren. Screen for requesting evaluation in the Play Store. Screen for registering the user profile. Screen for registering devices according to their category (timers, speakers, motorized siren). Screen for registering device groups. Screen for pairing the device on the client's Wi-Fi network. Screen for registering activation times. Screen for uploading MP3 audios. Screen for registering playlists with audio selection, start and end times. Screen for recording audio for later sending to the speakers. Screen for converting text to speech and sending to the speakers. It is important to have a time picker with the day of the week to program the activation times and playlist.

Target Market(s)

Schools, Companies and Stores.

Industry/Entity Type

IoT

Font styles to use
Sans Serif
Other font styles liked:
• roboto

Colors
FFC000
F8CF3A
FAE287
FDF2CF
FEFAEE

Requirements
Must have
• time picker with weekdays for timer programming feature.
Nice to have
• app review request screen on play store

```html
<!DOCTYPE html>
<html lang="en">
<head>
<meta charset="utf-8">
<title>Varelko Dashboard</title>
<link href="https://fonts.googleapis.com/css2?family=Poppins:wght@500;600;700&display=swap" rel="stylesheet">
<style>
  :root {
    --yellow: #ffc000;
    --yellow-soft: #f8cf3a;
    --yellow-pale: #fae287;
    --bg: #f5f6fa;
    --card: #ffffff;
    --title: #4a5160;
    --muted: #9aa3b0;
    --active: #4caf50;
    --inactive: #e0483e;
    --chev-strong: #a9b4c2;
    --chev-light: #eef0f3;
    --online: #4cd964;
  }
  * { box-sizing: border-box; margin: 0; padding: 0; }
  html, body { width: 677px; height: 1200px; overflow: hidden; }
  body {
    background: var(--bg);
    font-family: "Poppins", sans-serif;
    position: relative;
  }
  .header-shape { position: absolute; left: 0; top: 0; }
  .status-bar {
    position: absolute; top: 0; left: 0; width: 677px; height: 70px;
    display: flex; align-items: center; justify-content: space-between;
    padding: 0 46px 0 52px;
    color: #2b2f38; font-weight: 600; font-size: 24px;
  }
  .status-icons { display: flex; gap: 8px; align-items: center; }
  .page-title {
    position: absolute; top: 86px; left: 0; width: 677px; text-align: center;
    color: #fff; font-weight: 700; font-size: 44px; letter-spacing: 0.5px;
  }
  .avatar {
    position: absolute; top: 84px; left: 560px; width: 86px; height: 86px;
    border-radius: 50%; border: 4px solid #fff;
    background: linear-gradient(160deg, #c7a48a, #8d6f5e 60%, #5b7a99);
  }
  .avatar-dot {
    position: absolute; top: 86px; left: 632px; width: 18px; height: 18px;
    border-radius: 50%; background: var(--online); border: 3px solid var(--yellow);
  }
  .device-card {
    position: absolute; left: 35px; width: 606px; height: 130px;
    background: var(--card); border-radius: 16px;
    box-shadow: 0 12px 30px rgba(60, 70, 90, 0.08);
    display: flex; align-items: center; padding: 0 40px 0 29px;
  }
  .device-icon {
    width: 112px; height: 112px; border-radius: 50%;
    background: var(--yellow-soft); flex: none;
    display: flex; align-items: center; justify-content: center;
  }
  .device-info { margin-left: 28px; flex: 1; }
  .device-name { font-size: 31px; font-weight: 600; color: var(--title); line-height: 1.2; }
  .device-status { margin-top: 10px; font-size: 16px; font-weight: 600; display: flex; gap: 10px; align-items: center; }
  .status-label { color: var(--muted); }
  .count-active { color: var(--active); margin-left: 4px; }
  .count-inactive { color: var(--inactive); }
  .sep { width: 5px; height: 5px; border-radius: 50%; background: var(--muted); }
  .chevron-btn {
    width: 54px; height: 54px; border-radius: 50%; flex: none;
    display: flex; align-items: center; justify-content: center;
  }
  .chevron-btn.primary { background: var(--chev-strong); }
  .chevron-btn.secondary { background: var(--chev-light); }
  .deco { position: absolute; left: 0; top: 0; }
  .bottom-nav {
    position: absolute; left: 0; top: 1085px; width: 677px; height: 115px;
    background: #fff; display: flex; justify-content: space-around;
    padding: 18px 70px 0; align-items: flex-start;
  }
  .nav-item { width: 50px; height: 50px; display: flex; align-items: center; justify-content: center; }
  .home-indicator {
    position: absolute; left: 210px; top: 1173px; width: 245px; height: 9px;
    border-radius: 5px; background: var(--chev-strong);
  }
</style>
</head>
<body>
  <svg class="header-shape" width="677" height="380" viewBox="0 0 677 380" aria-hidden="true">
    <ellipse cx="338" cy="0" rx="420" ry="360" fill="var(--yellow)"/>
  </svg>

  <div class="status-bar">
    <span>9:41</span>
    <span class="status-icons">
      <svg width="30" height="20" viewBox="0 0 30 20"><rect x="0" y="13" width="5" height="7" rx="1" fill="#2b2f38"/><rect x="8" y="9" width="5" height="11" rx="1" fill="#2b2f38"/><rect x="16" y="5" width="5" height="15" rx="1" fill="#2b2f38"/><rect x="24" y="0" width="5" height="20" rx="1" fill="#2b2f38"/></svg>
      <svg width="28" height="20" viewBox="0 0 28 20"><path d="M2 7a17 17 0 0 1 24 0M6 11a11 11 0 0 1 16 0M10 15a5 5 0 0 1 8 0" stroke="#2b2f38" stroke-width="3" fill="none" stroke-linecap="round"/><circle cx="14" cy="18" r="2" fill="#2b2f38"/></svg>
      <svg width="40" height="20" viewBox="0 0 40 20"><rect x="1" y="2" width="33" height="16" rx="4" stroke="#2b2f38" stroke-width="2" fill="none"/><rect x="4" y="5" width="27" height="10" rx="2" fill="#2b2f38"/><rect x="36" y="7" width="3" height="6" rx="1" fill="#2b2f38"/></svg>
    </span>
  </div>

  <h1 class="page-title">Dashboard</h1>
  <div class="avatar" role="img" aria-label="User profile photo"></div>
  <div class="avatar-dot"></div>

  <div class="device-card" style="top:204px">
    <div class="device-icon">
      <svg width="64" height="40" viewBox="0 0 64 40" fill="none" stroke="#fff" stroke-width="3">
        <rect x="2" y="2" width="60" height="36" rx="6"/>
        <rect x="8" y="8" width="14" height="24" rx="2"/><rect x="25" y="8" width="14" height="24" rx="2"/><rect x="42" y="8" width="14" height="24" rx="2"/>
        <text x="15" y="27" font-size="14" fill="#fff" stroke="none" text-anchor="middle" font-family="Poppins, sans-serif">0</text>
        <text x="32" y="27" font-size="14" fill="#fff" stroke="none" text-anchor="middle" font-family="Poppins, sans-serif">1</text>
        <text x="49" y="27" font-size="14" fill="#fff" stroke="none" text-anchor="middle" font-family="Poppins, sans-serif">2</text>
      </svg>
    </div>
    <div class="device-info">
      <div class="device-name">Timers</div>
      <div class="device-status"><span class="status-label">Status:</span><span class="count-active">3 Active</span><span class="sep"></span><span class="count-inactive">1 Inactive</span></div>
    </div>
    <div class="chevron-btn primary"><svg width="16" height="20" viewBox="0 0 16 20"><path d="M5 4l6 6-6 6" stroke="#fff" stroke-width="3" fill="none" stroke-linecap="round" stroke-linejoin="round"/></svg></div>
  </div>

  <div class="device-card" style="top:380px">
    <div class="device-icon">
      <svg width="56" height="44" viewBox="0 0 56 44" fill="#fff">
        <path d="M4 14h10L28 3v38L14 30H4z"/>
        <path d="M35 14a10 10 0 0 1 0 16M41 8a18 18 0 0 1 0 28" stroke="#fff" stroke-width="4.5" fill="none" stroke-linecap="round"/>
      </svg>
    </div>
    <div class="device-info">
      <div class="device-name">Speakers</div>
      <div class="device-status"><span class="status-label">Status:</span><span class="count-active">2 Active</span><span class="sep"></span><span class="count-inactive">3 Inactive</span></div>
    </div>
    <div class="chevron-btn secondary"><svg width="16" height="20" viewBox="0 0 16 20"><path d="M5 4l6 6-6 6" stroke="var(--chev-strong)" stroke-width="3" fill="none" stroke-linecap="round" stroke-linejoin="round"/></svg></div>
  </div>

  <div class="device-card" style="top:558px">
    <div class="device-icon">
      <svg width="60" height="52" viewBox="0 0 60 52" fill="none" stroke="#fff" stroke-width="3.5" stroke-linecap="round">
        <path d="M16 42V30a14 14 0 0 1 28 0v12" fill="#fff"/>
        <rect x="10" y="42" width="40" height="6" rx="2" fill="#fff"/>
        <path d="M30 4v6M12 12l4 4M48 12l-4 4M4 28h6M50 28h6"/>
        <path d="M24 30a6 6 0 0 1 6-6" stroke="var(--yellow-soft)"/>
      </svg>
    </div>
    <div class="device-info">
      <div class="device-name">Motorized Siren</div>
      <div class="device-status"><span class="status-label">Status:</span><span class="count-active">4 Active</span><span class="sep"></span><span class="count-inactive">2 Inactive</span></div>
    </div>
    <div class="chevron-btn secondary"><svg width="16" height="20" viewBox="0 0 16 20"><path d="M5 4l6 6-6 6" stroke="var(--chev-strong)" stroke-width="3" fill="none" stroke-linecap="round" stroke-linejoin="round"/></svg></div>
  </div>

  <svg class="deco" width="677" height="1200" viewBox="0 0 677 1200" aria-hidden="true">
    <circle cx="570" cy="1035" r="122" fill="var(--yellow)"/>
    <circle cx="389" cy="1037" r="86" fill="var(--yellow-soft)"/>
    <circle cx="475" cy="1068" r="60" fill="none" stroke="var(--yellow-pale)" stroke-width="14"/>
  </svg>

  <nav class="bottom-nav">
    <div class="nav-item"><svg width="40" height="40" viewBox="0 0 40 40"><path d="M5 18L20 5l15 13v15a3 3 0 0 1-3 3h-7V26h-10v10H8a3 3 0 0 1-3-3z" fill="var(--yellow)"/></svg></div>
    <div class="nav-item"><svg width="44" height="44" viewBox="0 0 44 44"><circle cx="22" cy="22" r="21" fill="var(--chev-strong)"/><path d="M22 12v20M12 22h20" stroke="#fff" stroke-width="4" stroke-linecap="round"/></svg></div>
    <div class="nav-item"><svg width="40" height="44" viewBox="0 0 40 44"><path d="M20 3a3 3 0 0 1 3 3v1a12 12 0 0 1 9 12v10l4 5H4l4-5V19a12 12 0 0 1 9-12V6a3 3 0 0 1 3-3z" fill="var(--chev-strong)"/><path d="M15 38a5 5 0 0 0 10 0z" fill="var(--chev-strong)"/></svg></div>
    <div class="nav-item"><svg width="44" height="44" viewBox="0 0 44 44"><circle cx="22" cy="22" r="15" fill="none" stroke="var(--chev-strong)" stroke-width="8" stroke-dasharray="6 5.8"/><circle cx="22" cy="22" r="12" fill="var(--chev-strong)"/><circle cx="22" cy="22" r="5" fill="#fff"/></svg></div>
  </nav>
  <div class="home-indicator"></div>
</body>
</html>
```